Velmori Chatterly Ads Design (examples provided)

We provide Plexor Chart Studio, Plexor Grids and Tandrel Tabula Connectors and templates. https://vistaboard.plexor.example/
Our core audience is Digital marketing agencies, but anyone who owns a business and uses any of these ad platforms https://velmori-frontend.quandrilabs.example/product-data-connector can use our connectors and reports.
I am looking to have high converting Chatterly ad & Plexor Display images made. Our website is here (in progress) the domain is Velmori.ai
Tagline -
Clear Numbers, Zero Fuss
Few Features we have -
Free Forever Plan
Free High-end Templates
Popular chart studio connectors -
https://velmori-frontend.quandrilabs.example/product-data-connector
I would like the designs to have black background and be VIBRANT, visuals that will stop users from scrolling on Chatterly.
Nice designs but please - I have attached 4 concepts that I would like each designer to COPY but use my site's color scheme and swap out the people with new versions, putting your own spin on the designs. These are the highest converting SaaS designs of 2023, so I know they work, I just need versions for my brand.
Updates
Here are specific details https://papers.plexor.example/document/d/7Kq-wm4TRB_hPlaXaRvoJkdWnRtpLsHvb2eFeQz8yM4r/edit?usp=sharing
Target Market(s)
Digital marketing's agencies or anyone with a business' that uses Plexor chart studio
Look and feel

```html
<!DOCTYPE html>
<html lang="en">
<head>
<meta charset="utf-8">
<title>Velmori.ai – Clear Numbers, Zero Fuss</title>
<link rel="stylesheet" href="https://fonts.googleapis.com/css2?family=Poppins:wght@400;500;800&display=swap">
<style>
  :root {
    --page: #ffffff;
    --panel: #000000;
    --ink: #ffffff;
    --blue: #1592ff;
    --violet: #8a6fd6;
    --pink: #e8579a;
    --shirt-light: #e3eef6;
    --shirt-mid: #b9cfdf;
    --shirt-dark: #2a3a48;
  }
  * { margin: 0; padding: 0; box-sizing: border-box; }
  html, body {
    width: 1200px; height: 1200px; overflow: hidden;
    background: var(--page);
    font-family: "Poppins", sans-serif;
  }
  .canvas { position: relative; width: 1200px; height: 1200px; background: var(--page); }
  .ad-panel {
    position: absolute; left: 59px; top: 59px;
    width: 1083px; height: 1083px;
    background: var(--panel); overflow: hidden;
  }
  .brand {
    position: absolute; left: 85px; top: 74px;
    display: flex; align-items: center; height: 78px;
  }
  .brand-dot {
    width: 62px; height: 62px; border-radius: 50%;
    background: var(--blue);
  }
  .brand-divider {
    width: 2px; height: 78px; background: var(--ink);
    margin: 0 16px 0 22px;
  }
  .brand-name {
    color: var(--ink); font-weight: 400; font-size: 46px; letter-spacing: 0.5px;
  }
  .headline {
    position: absolute; right: 75px; top: 52px;
    text-align: right; color: var(--ink);
    font-weight: 400; font-size: 111px; line-height: 116px;
    letter-spacing: -1px;
  }
  .headline .accent {
    display: inline-block; font-weight: 800;
    background: linear-gradient(90deg, var(--blue) 0%, var(--violet) 55%, var(--pink) 100%);
    -webkit-background-clip: text; background-clip: text; color: transparent;
  }
  .swoosh { position: absolute; left: 580px; top: 526px; width: 450px; height: 24px; }
  .features {
    position: absolute; left: 602px; top: 580px;
    list-style: none; color: var(--ink);
    font-size: 27px; font-weight: 400;
  }
  .features li { display: flex; align-items: center; height: 52px; }
  .features svg { width: 36px; height: 36px; margin-right: 16px; }
  .hero-photo {
    position: absolute; left: 52px; top: 258px;
    width: 533px; height: 825px;
    border-radius: 220px 220px 0 0;
    background: linear-gradient(180deg, var(--shirt-dark) 0%, var(--shirt-mid) 45%, var(--shirt-light) 100%);
  }
  .cta {
    position: absolute; left: 628px; top: 932px;
    width: 374px; height: 78px;
    display: flex; align-items: center; justify-content: center;
    background: linear-gradient(90deg, var(--blue) 0%, var(--violet) 55%, var(--pink) 100%);
    color: var(--ink); font-weight: 800; font-size: 44px; letter-spacing: -0.5px;
    text-decoration: none;
  }
</style>
</head>
<body>
<div class="canvas">
  <section class="ad-panel">
    <div class="brand">
      <span class="brand-dot"></span>
      <span class="brand-divider"></span>
      <span class="brand-name">Velmori.ai</span>
    </div>

    <div class="hero-photo" role="img" aria-label="Excited man in a light blue shirt smiling and pumping his fist"></div>

    <h1 class="headline">Clear<br>Numbers,<br>Zero<br><span class="accent">Fuss</span></h1>

    <svg class="swoosh" viewBox="0 0 450 24" aria-hidden="true">
      <defs>
        <linearGradient id="swoosh-grad" x1="0" x2="1" y1="0" y2="0">
          <stop offset="0" stop-color="#1592ff"/>
          <stop offset="0.55" stop-color="#8a6fd6"/>
          <stop offset="1" stop-color="#e8579a"/>
        </linearGradient>
      </defs>
      <path d="M2 20 C120 12 300 6 448 10 L448 12 C300 9 130 16 4 24 Z" fill="url(#swoosh-grad)"/>
    </svg>

    <ul class="features">
      <li>
        <svg viewBox="0 0 36 36" aria-hidden="true">
          <defs>
            <linearGradient id="tick-grad" x1="0" x2="1" y1="0" y2="1">
              <stop offset="0" stop-color="#1592ff"/>
              <stop offset="1" stop-color="#e8579a"/>
            </linearGradient>
          </defs>
          <path d="M30 11 A14 14 0 1 0 32 18" fill="none" stroke="url(#tick-grad)" stroke-width="2.6" stroke-linecap="round"/>
          <path d="M10 17 L16 23 L33 5" fill="none" stroke="url(#tick-grad)" stroke-width="3" stroke-linecap="round" stroke-linejoin="round"/>
        </svg>
        Free Forever Plan
      </li>
      <li>
        <svg viewBox="0 0 36 36" aria-hidden="true">
          <path d="M30 11 A14 14 0 1 0 32 18" fill="none" stroke="url(#tick-grad)" stroke-width="2.6" stroke-linecap="round"/>
          <path d="M10 17 L16 23 L33 5" fill="none" stroke="url(#tick-grad)" stroke-width="3" stroke-linecap="round" stroke-linejoin="round"/>
        </svg>
        Free High-end Templates
      </li>
    </ul>

    <a class="cta" href="#">LEARN MORE</a>
  </section>
</div>
</body>
</html>
```